TL - business card

Tallow Partners is an insurance brokerage firm, inovative, proactive, vigorous, which aims to become the leader of the insurance brokers in Anfrica. We should like to get some designs which should be avoided also in Gray / Metallic for the Administration and Orange / Blue for the Managers (ike in the picture sent). The Blue / Green logo is not the correct one, but the source of the file. Please adjust the color accordingly for the business cards. 1 / Orange / Blue 2 / Gray / Metallic We want something classic but which is transmitted strenght, inovation, modernity and most of all, rapidity. We want something start-up like, very punchy and catching eye remaining profesional at the same time. Name: Dorian Whitlock Function: Managing Director Address: N ° 17/18 Rua Veloso - R / C 2B Direita - Bairro Mutamba - Luanda Tel: (+244) 947 582 316 Email: dorian.whitlock@tallow-p.example Website: www.tallow-p. example We want classic in the front and creative, colorfull at the back. The cards will be printed in relief, with very high quality of paper.
Insurance Broker
Colors
Designer to choose colors to be used in the design.

```html
<!DOCTYPE html>
<html lang="en">
<head>
<meta charset="utf-8">
<title>Tallow Partners – Business Card</title>
<link href="https://fonts.googleapis.com/css2?family=Lato:wght@400;700;900&family=Roboto:wght@700&display=swap" rel="stylesheet">
<style>
  :root {
    --brand-blue: #0a7bc2;
    --accent-red: #e0402a;
    --accent-orange: #f08a3e;
    --text-grey: #555555;
    --paper: #ffffff;
    --backdrop: #cfcfcf;
  }
  * { box-sizing: border-box; margin: 0; padding: 0; }
  html, body {
    width: 1125px; height: 1200px; overflow: hidden;
    background: var(--backdrop);
    font-family: "Lato", sans-serif;
  }
  .canvas { position: relative; width: 1125px; height: 1200px; }
  .card {
    position: absolute; left: 178px; width: 768px; height: 437px;
    overflow: hidden;
  }
  .card--front { top: 140px; background: var(--paper); }
  .card--back { top: 626px; background: var(--brand-blue); }

  .band { position: absolute; background: var(--brand-blue); top: 187px; height: 62px; }
  .band--left { left: 0; width: 51px; }
  .band--address { left: 384px; right: 0; padding: 13px 0 0 19px; color: #fff; font-size: 17px; line-height: 22px; }
  .band--address .line-1 { padding-left: 4px; }

  .divider { position: absolute; left: 384px; width: 2px; background: var(--accent-red); }
  .divider--name { top: 99px; height: 60px; }
  .divider--contact { top: 273px; height: 88px; }

  .brand-mark { position: absolute; text-align: center; }
  .brand-mark .ring { display: block; margin: 0 auto; }
  .card--front .brand-mark { left: 70px; width: 266px; top: 154px; }
  .card--front .brand-name { color: var(--brand-blue); font-weight: 900; font-size: 25px; margin-top: 8px; letter-spacing: 0.5px; }
  .card--back .brand-mark { left: 0; right: 0; top: 141px; }
  .card--back .brand-name { color: #fff; font-weight: 900; font-size: 31px; margin-top: 10px; letter-spacing: 0.5px; }

  .holder { position: absolute; left: 403px; top: 100px; }
  .holder-name { font-family: "Roboto", sans-serif; font-weight: 700; font-size: 29px; color: var(--brand-blue); letter-spacing: 1.6px; line-height: 34px; }
  .holder-role { font-size: 18px; color: var(--text-grey); margin-top: 4px; }

  .contacts { position: absolute; left: 403px; top: 276px; list-style: none; }
  .contacts li { display: flex; align-items: center; height: 30px; font-size: 18px; color: var(--text-grey); }
  .contacts svg { width: 14px; height: 14px; margin-right: 13px; fill: var(--brand-blue); flex: none; }

  .back-url { position: absolute; left: 0; right: 0; top: 384px; text-align: center; color: #fff; font-size: 17px; }
</style>
</head>
<body>
<div class="canvas">

  <section class="card card--front">
    <div class="band band--left"></div>

    <div class="brand-mark">
      <svg class="ring" width="96" height="96" viewBox="0 0 96 96"><circle cx="48" cy="48" r="42" fill="none" stroke="var(--accent-orange)" stroke-width="6"/></svg>
      <div class="brand-name">Tallow Partners</div>
    </div>

    <div class="divider divider--name"></div>
    <div class="holder">
      <h1 class="holder-name">Dorian Whitlock</h1>
      <p class="holder-role">Managing Director</p>
    </div>

    <div class="band band--address">
      <div class="line-1">N ° 17/18 Rua Veloso - R / C 2B</div>
      <div>Direita - Bairro Mutamba - Luanda</div>
    </div>

    <div class="divider divider--contact"></div>
    <ul class="contacts">
      <li><svg viewBox="0 0 24 24"><path d="M6.6 10.8a15.1 15.1 0 0 0 6.6 6.6l2.2-2.2a1 1 0 0 1 1-.25 11.4 11.4 0 0 0 3.6.57 1 1 0 0 1 1 1V20a1 1 0 0 1-1 1A17 17 0 0 1 3 4a1 1 0 0 1 1-1h3.5a1 1 0 0 1 1 1c0 1.25.2 2.45.57 3.57a1 1 0 0 1-.25 1z"/></svg>(+244) 947 582 316</li>
      <li><svg viewBox="0 0 24 24"><path d="M2 4h20v16H2zm2 2v.5l8 5.5 8-5.5V6zm0 3v9h16V9l-8 5.5z"/></svg>dorian.whitlock@tallow-p.example</li>
      <li><svg viewBox="0 0 24 24"><path d="M12 2a10 10 0 1 0 0 20 10 10 0 0 0 0-20zm-1 17.9A8 8 0 0 1 4.2 10l4.8 4.8v1a2 2 0 0 0 2 2zm6.9-2.5A2 2 0 0 0 16 16h-1v-3a1 1 0 0 0-1-1H8v-2h2a1 1 0 0 0 1-1V7h2a2 2 0 0 0 2-2v-.4a8 8 0 0 1 2.9 12.8z"/></svg>www.tallow-p. example</li>
    </ul>
  </section>

  <section class="card card--back">
    <div class="brand-mark">
      <svg class="ring" width="114" height="114" viewBox="0 0 114 114"><circle cx="57" cy="57" r="50" fill="none" stroke="#ffffff" stroke-width="7"/></svg>
      <div class="brand-name">Tallow Partners</div>
    </div>
    <p class="back-url">www.tallow-p. example</p>
  </section>

</div>
</body>
</html>
```